VELTAR WEBSITE

need to create a new website for VELTAR ltd
the company deals with all aspects of safety products & safety wear
we need a simple website to show
ideas can be taken from following website whose products we shall distribute in kenya
www.kwr.co.uk
www.dorvik.eu
www.brimtoolsupplyco.com
www.gardvalewerks.co.za

we need following tabs
1) home - basic company information
2) products - broken down to following categories ie gloves, head protection, ear protection, mouth protection, foot protection
3) contacts

the company profile is a reputable company dealing with all aspects of safety, HSE (health and safety equipment), and PPE (personal protective equipment)

the website should have the dorvik logo for which we are an authorized distributor.
the dorvi industrial range writeup can be picked from their website
Updates

Dear Designers, i shall be able to choose a final design in 2 weeks, sorry i have not been able to finalise this due to a personal reason

Target Market(s)

the buyers are all types of industry who care for their employees safety

Industry/Entity Type

Industrial

Requirements
Must have
• clean look, fresh look, user freindly
Nice to have
• clear images, quick links etc

```html
<!DOCTYPE html>
<html lang="en">
<head>
<meta charset="utf-8">
<title>VELTAR – Safety Products &amp; Safety Wear</title>
<link href="https://fonts.googleapis.com/css2?family=Ubuntu:ital,wght@0,300;0,400;0,500;1,300;1,400&display=swap" rel="stylesheet">
<style>
:root{
  --brand:#f3b400;
  --ink:#2c2c2c;
  --text:#333;
  --line:#e3e3e3;
  --dots:#cfcfcf;
  --navy:#1f2b38;
  --footer:#2b2b2b;
  --panel:#fafafa;
}
*{box-sizing:border-box;margin:0;padding:0}
html,body{width:1067px;height:1200px;overflow:hidden;background:#fff}
body{position:relative;font-family:"Ubuntu",sans-serif;color:var(--text)}
.abs{position:absolute}

/* header */
.brand{left:116px;top:52px;display:flex;align-items:center;gap:10px}
.brand-mark{width:30px;height:30px;background:var(--brand)}
.brand-name{font-size:38px;font-weight:500;color:var(--navy);letter-spacing:1px}
.contact{right:118px;top:26px;font-size:16px;line-height:23px;color:var(--ink)}
.contact span{color:#555;display:inline-block;margin-left:6px}
.contact .fax span{margin-left:24px}
.follow{left:861px;top:77px;font-size:16.5px;color:var(--ink)}
.social{left:842px;top:105px;display:flex;gap:6px}
.social span{width:22px;height:22px;border:1px solid #ccc;border-radius:2px;background:linear-gradient(#fafafa,#e6e6e6)}

/* nav */
.nav{left:107px;top:151px;width:854px;height:45px;border:1px solid #eee;border-bottom:2px solid var(--line);background:#fff}
.nav a{position:absolute;top:13px;font-size:15px;color:#444;text-decoration:none}
.nav a.active{color:var(--brand)}
.search{position:absolute;left:642px;top:11px;width:201px;height:24px;border:1px solid #e4e4e4;background:#fafafa;font-size:11.5px;color:#999;padding:5px 6px}
.search svg{position:absolute;right:6px;top:4px}

/* hero */
.hero{left:107px;top:196px;width:854px;height:322px;background:
  radial-gradient(ellipse 22% 45% at 68% 55%,rgba(70,52,42,.55) 0%,rgba(70,52,42,0) 100%),
  radial-gradient(ellipse 22% 45% at 87% 55%,rgba(70,52,42,.55) 0%,rgba(70,52,42,0) 100%),
  radial-gradient(ellipse at 30% 5%,#ffb24a 0%,#f08a1e 35%,rgba(240,138,30,0) 65%),
  linear-gradient(180deg,#f6a54b 0%,#e7843a 45%,#c57650 70%,#9e6a5a 100%)}
.caption{left:117px;top:276px;width:295px;height:161px;background:rgba(60,45,35,.68);padding:10px 10px}
.caption h2{font-weight:400;font-size:30px;color:#fff;letter-spacing:.5px;line-height:36px}
.caption p{font-size:12.5px;line-height:19px;color:#f1e4d4;margin-top:7px;letter-spacing:-.3px;max-width:268px}
.btn-yellow{display:inline-block;margin-top:10px;background:linear-gradient(#ffd23a,#f0b000);border:1px solid #e6a800;color:#5a4300;font-size:12.5px;padding:5px 6px;border-radius:2px}

/* section heading */
.heading{display:flex;align-items:center;gap:6px;font-weight:400;color:var(--ink);white-space:nowrap}
.heading::after{content:"";flex:1;height:4px;margin-top:6px;background-image:radial-gradient(circle,var(--dots) 0.8px,transparent 1px);background-size:3px 4px}
.heading em{font-style:normal;color:var(--brand)}

.welcome{left:116px;top:545px;width:587px}
.welcome .heading{font-size:22px}
.welcome p{font-size:11.5px;line-height:19.5px;color:#333;margin-top:8px;max-width:570px}
.welcome p + p{margin-top:19px}
.btn-dark{display:inline-block;margin-top:7px;background:linear-gradient(#3a3a3a,#151515);color:#fff;font-size:12.5px;padding:6px 8px;border-radius:3px;border:1px solid #000}

.login{left:744px;top:548px;width:206px}
.login .heading{font-size:19px}
.login label{display:block;font-size:10px;color:#777;margin:15px 0 5px 3px}
.field{width:199px;height:24px;margin-left:4px;border:1px solid #e5e5e5;background:#fff;box-shadow:inset 0 1px 2px #eee}
.login .label2{margin-top:7px}
.login-row{display:flex;justify-content:space-between;align-items:center;margin-top:26px}
.btn-login{background:linear-gradient(#3a3a3a,#151515);color:#fff;font-size:12.5px;padding:5px 16px;border-radius:2px;border:1px solid #000}
.forgot{font-size:10.5px;color:var(--brand);text-decoration:underline;margin-right:8px}

.products{left:116px;top:754px;width:834px}
.products .heading{font-size:19.5px}
.product-grid{position:absolute;top:34px;left:0;display:flex;gap:13px}
.product{width:198px;height:111px;border:1px solid #e8e8e8;background:#fff}
.product.helmet{background:radial-gradient(ellipse 38% 42% at 50% 55%,rgba(38,100,210,.85) 0%,rgba(38,100,210,.35) 60%,rgba(38,100,210,0) 100%),#fff}
.product.gloves{background:radial-gradient(ellipse 36% 46% at 50% 50%,rgba(40,125,230,.8) 0%,rgba(40,125,230,.3) 60%,rgba(40,125,230,0) 100%),#fff}
.product.mask{background:radial-gradient(ellipse 36% 40% at 50% 52%,rgba(120,108,80,.85) 0%,rgba(120,108,80,.3) 60%,rgba(120,108,80,0) 100%),#fff}
.product.kit{background:linear-gradient(120deg,#e8cf2e 0%,#d8cfa6 40%,#6d6a64 70%,#c3bfb6 100%)}

.features{left:116px;top:928px;width:400px}
.features .heading{font-size:19.5px}
.features ul{list-style:none;margin-top:11px}
.features li{display:flex;align-items:center;gap:8px;height:49px;border-bottom:1px solid var(--line);font-size:15.5px;color:#333;padding-top:2px}
.plus{width:18px;height:18px;border-radius:50%;background:var(--brand);color:#fff;font-size:15px;line-height:18px;text-align:center;font-weight:500;flex:none}

.testimonials{left:540px;top:928px;width:410px}
.testimonials .heading{font-size:19.5px;padding-right:42px}
.arrows{position:absolute;right:0;top:7px;display:flex;gap:4px}
.arrows span{width:15px;height:15px;border-radius:50%;background:#555;display:flex;align-items:center;justify-content:center}
.quote{margin-top:14px;border:1px solid #ddd;border-radius:3px;background:var(--panel);padding:14px 30px 14px 41px;position:relative;font-style:italic;font-weight:300;font-size:12.9px;line-height:17.8px;color:#777}
.quote::before{content:"\201C";position:absolute;left:22px;top:6px;font-size:30px;font-style:normal;font-weight:500;color:var(--brand)}
.author{display:flex;justify-content:space-between;align-items:flex-end;margin-top:10px}
.author .name{font-size:12.5px;color:var(--brand)}

.footer{left:0;top:1162px;width:1067px;height:38px;background:var(--footer);color:#bbb;font-size:10.5px}
.footer .copy{position:absolute;left:116px;top:13px}
.footer .links{position:absolute;right:117px;top:13px}
</style>
</head>
<body>

<header>
  <div class="abs brand"><span class="brand-mark"></span><span class="brand-name">VELTAR</span></div>
  <div class="abs contact">
    <div>Phone:<span>(800) 555-0142</span></div>
    <div class="fax">Fax:<span>(800) 555-0142</span></div>
  </div>
  <div class="abs follow">Follow Us:</div>
  <div class="abs social" aria-label="Social links"><span></span><span></span><span></span><span></span></div>
</header>

<nav class="abs nav">
  <a class="active" style="left:13px">Home</a>
  <a style="left:97px">Products</a>
  <a style="left:201px">About Us</a>
  <a style="left:306px">Clients</a>
  <a style="left:395px">Agencies</a>
  <a style="left:498px">Contact Us</a>
  <div class="search">Search...
    <svg width="16" height="16" viewBox="0 0 16 16"><circle cx="6.5" cy="6.5" r="4.5" fill="none" stroke="#bbb" stroke-width="2"/><line x1="10" y1="10" x2="14.5" y2="14.5" stroke="#bbb" stroke-width="2.5"/></svg>
  </div>
</nav>

<section class="abs hero" role="img" aria-label="Photo of a pair of worn leather safety boots standing on sand against an orange sunset sky"></section>
<div class="abs caption">
  <h2>FOOT PROTECTION</h2>
  <p>Contrairement à une opinion répandue, le Lorem Ipsum n'est pas simplement du texte aléatoire. Ses racines dans latine classique datant.</p>
  <span class="btn-yellow">Know More</span>
</div>

<section class="abs welcome">
  <h1 class="heading">Welcome To&nbsp;<em>VELTAR</em></h1>
  <p>Contrairement à une opinion répandue, le Lorem Ipsum n'est pas simplement du texte aléatoire. Il trouve ses racines dans une oeuvre de la littérature latine classique datant deContrairement à une opinion répandue. Lorem Ipsum n'est pas simplement du texte aléatoire.</p>
  <p>Contrairement à une opinion répandue, Latine classique datant. Il trouve ses racines dans une oeuvre de la litté-rature latine classique datant deContrairement à une opinion répandue.</p>
  <span class="btn-dark">READ MORE</span>
</section>

<section class="abs login">
  <h2 class="heading">Veltar Login</h2>
  <label>User Name</label>
  <div class="field"></div>
  <label class="label2">Password</label>
  <div class="field"></div>
  <div class="login-row"><span class="btn-login">Login</span><span class="forgot">Forgot Login?</span></div>
</section>

<section class="abs products">
  <h2 class="heading">Our Products</h2>
  <div class="product-grid">
    <div class="product helmet" role="img" aria-label="Photo of a blue safety hard hat"></div>
    <div class="product gloves" role="img" aria-label="Photo of a pair of blue insulated protective gloves"></div>
    <div class="product mask" role="img" aria-label="Photo of an olive half-face protective mask"></div>
    <div class="product kit" role="img" aria-label="Photo of assorted safety gear: yellow helmet, goggles, boots, gloves and respirator"></div>
  </div>
</section>

<section class="abs features">
  <h2 class="heading">Veltar Specialized Protective</h2>
  <ul>
    <li><span class="plus">+</span>Lorem ipsum dolor sit amet consectetur.</li>
    <li><span class="plus">+</span>Adipsicing elit, Sed do euismod</li>
    <li><span class="plus">+</span>Tempor incididunt ut labore et dolor magna aliqua</li>
    <li><span class="plus">+</span>Ut enim ad minim veniam</li>
  </ul>
</section>

<section class="abs testimonials">
  <h2 class="heading">Testimonials</h2>
  <div class="arrows">
    <span><svg width="7" height="8" viewBox="0 0 7 8"><path d="M5 0.5 1.5 4 5 7.5" fill="none" stroke="#fff" stroke-width="1.6"/></svg></span>
    <span><svg width="7" height="8" viewBox="0 0 7 8"><path d="M2 0.5 5.5 4 2 7.5" fill="none" stroke="#fff" stroke-width="1.6"/></svg></span>
  </div>
  <blockquote class="quote">Lorem ipsum dolor sit amet, consectetur adipisicing elit, sed do eiusmod tempor incididunt ut labore et dolore magna aliqua. Ut enim ad minim veniam, quis nostrud exercitation ullamco laboris nisi ut aliquip ex ea commodo consequat. Duis aute irure dolor in reprehenderit in voluptate velit esse cillum dolore eu fugiat nulla pariatur.</blockquote>
  <div class="author">
    <svg width="32" height="32" viewBox="0 0 32 32" aria-hidden="true"><circle cx="16" cy="10" r="7" fill="#b5b5b5"/><path d="M2 32 C2 22 8 19 16 19 C24 19 30 22 30 32 Z" fill="#b5b5b5"/></svg>
    <span class="name">Marten Oakes</span>
  </div>
</section>

<footer class="abs footer">
  <span class="copy">Copyright © 2013&nbsp; All Rights Reserved</span>
  <span class="links">Terms &amp; Condition&nbsp; |&nbsp; Privacy Policy</span>
</footer>

</body>
</html>
```